Residential Mortgage Leader needs Wordpress Design

Looking for a home page website design for a client. We develop using the WordPress platform and would prefer the design be at least loosely based on an existing WordPress template. Attached files have many notes from our creative brief with client. The site must be responsive. Approved, basic wireframe attached. There is room for interpretation.

Existing web site: http://www.marisolkettering.example/

The Marisol Kettering Team relies on strong systems to deliver an on-time, done-right, friendly experience. Marisol offers mortgages and refinancing services throughout the United States. She is a successful Brookvale Funding agent who strives to be an active part of her community. She would like to focus the site on her team, rather than just her.

Difference makers...
When you work with the Marisol Kettering team you get a high level of expertise and a friendly experience.

She has amazing credentials. Marisol is widely recognized as a top producer for her company, and has earned a number of awards and honors for her customer service.

Marisol's team is very engaged and enjoys sharing social comments or photos from their community.

Imagery:
* Friendly, warm imagery, preferably of her team or an image to represent her team
* Clean and crisp
* Professional / Experts in mortgage and refinance
* Clean / Good use of white space
Updates

When possible, please use imagery from the DFW area. The client mentioned they would prefer not to see stock images. Thanks.

Amend that- creative use of stock images, however, is fine. A few designs have used stock imagery, but in a well-considered manner.

We added some photos and graphics that are local. We are Dallas / Ft. Worth, Plano, Frisco, Texas. We also added some examples of photos to use for the "In the Community" area. Stock photos of business folks just doesn't fit there. Thanks!

Target Market(s)

They service a lot of builders, but also work with homeowners. Their typical client is usually a woman searching for mortgage services online. She typically has a family and may refer her husband to Marisol's team. Keep in mind, however, they also see a number of other scenarios. Most of their clients are middle to high-end borrowers.

Industry/Entity Type

It Company

Requirements
Must have
• Design should be developed using program such as Photoshop or Fireworks or Illustrator as last preference. Ideally, the design would be based on an existing responsive WordPress theme, which we would customize. You must include the name of the target theme. The footer should include lots of space for disclaimers and legal language. Site navigation should include these choices: "Home, About, Builders, Mortgage Info, Approval, Blog, Contact"
Nice to have
• Blog, social media and photos area. Use of the already approved style prototype with colors and fonts (Lato- a Google font, Times New Roman and Cookie-a decorative Google font). However, we are open to interpretation.
Should not have
• Hard to read fonts or a lack of white space.

```html
<!DOCTYPE html>
<html lang="en">
<head>
<meta charset="utf-8">
<title>Brookvale Funding – Home</title>
<link href="https://fonts.googleapis.com/css2?family=Lato:wght@300;400;700&display=swap" rel="stylesheet">
<style>
:root{
  --red:#c9241b;
  --blue:#1a8ac6;
  --btn-blue:#2a9be0;
  --ink:#333;
  --body:#555;
  --topbar:#e9e9e9;
  --hero-panel:#5c5c5e;
  --cred-panel:#f1f1f1;
  --footer:#1f1f1f;
  --footer-text:#9a9a9a;
  --line:#e2e2e2;
}
*{margin:0;padding:0;box-sizing:border-box}
html,body{width:854px;height:1200px;overflow:hidden;background:#fff}
body{position:relative;font-family:'Lato',sans-serif;color:var(--ink)}
h1,h2,h3{font-weight:400}
.abs{position:absolute}
.topbar{left:0;top:0;width:854px;height:37px;background:var(--topbar);border-bottom:1px solid #ddd}
.contact-item{top:12px;font-size:8px;color:#a5a5a5;display:flex;align-items:center;gap:6px}
.contact-icon{width:13px;height:13px;background:#555;display:inline-block}
.social-dots{top:11px;left:630px;display:flex;gap:6px}
.social-dots span{width:15px;height:15px;border-radius:50%;background:#aaa}
.brand{left:0;width:854px;top:58px;text-align:center}
.brand-name{font-size:16px;font-weight:700;color:var(--red);display:inline-flex;align-items:center;gap:6px}
.brand-mark{width:10px;height:10px;background:var(--red)}
.brand-tag{font-size:7px;color:#555;margin-top:1px}
.nav{left:71px;top:118px;width:712px;height:30px;border-top:1px solid var(--line);border-bottom:1px solid var(--line);display:flex;justify-content:center;align-items:center}
.nav a{font-size:9px;font-weight:700;color:#222;text-decoration:none;padding:4px 10px;margin:0 7px}
.nav a.active{background:var(--red);color:#fff}
.hero-shadow{left:90px;top:425px;width:674px;height:16px;border-radius:50%;box-shadow:0 8px 10px rgba(0,0,0,.35)}
.hero-photo{left:71px;top:167px;width:463px;height:266px;
  background:
    radial-gradient(ellipse 46% 30% at 22% 88%,#4f7a34 0%,rgba(79,122,52,0) 100%),
    radial-gradient(ellipse 40% 28% at 80% 90%,#5b8a3c 0%,rgba(91,138,60,0) 100%),
    radial-gradient(ellipse 36% 22% at 52% 20%,#8d8179 0%,rgba(141,129,121,0) 100%),
    radial-gradient(ellipse 40% 46% at 52% 55%,#b7785a 0%,rgba(183,120,90,0) 100%),
    linear-gradient(180deg,#4f8fd3 0%,#9fc2e6 28%,#c9a08a 50%,#a36b4f 68%,#6f7f47 86%,#c9bba0 100%)}
.hero-panel{left:534px;top:167px;width:249px;height:266px;background:var(--hero-panel);color:#fff;padding:0 18px}
.hero-title{font-size:19px;margin-top:27px}
.hero-text{font-size:8.3px;font-weight:300;line-height:16px;margin-top:18px;padding-left:2px;color:#f2f2f2}
.hero-actions{display:flex;align-items:center;gap:12px;margin-top:26px}
.btn-start{background:var(--btn-blue);color:#fff;font-size:12.5px;padding:5px 14px;border-radius:2px}
.btn-know{font-size:14px}
.cred{left:71px;top:470px;width:712px;height:230px;border:1px solid #eee}
.cred-panel{left:71px;top:470px;width:267px;height:230px;background:var(--cred-panel)}
.cred-notch{left:338px;top:470px}
.cred-title{left:87px;top:496px;font-size:15px;color:var(--red)}
.cred-text{left:84px;top:534px;width:236px;font-size:8.3px;font-weight:300;line-height:16px;color:var(--body)}
.feature{width:200px;text-align:center}
.feature-icon{display:block;margin:0 auto}
.feature-title{font-size:16px;font-weight:300;margin-top:18px;color:#444}
.feature-text{font-size:8.3px;font-weight:300;line-height:16px;color:var(--body);margin-top:10px}
.btn-more{display:inline-block;background:#333;color:#fff;font-size:8.5px;padding:2px 11px;margin-top:23px}
.sec-title{top:726px;font-size:15px;padding-bottom:4px;border-bottom:2px solid}
.blog-item{left:73px;width:210px;border-left:3px solid #333;padding-left:11px}
.blog-item h3{font-size:13.5px;font-weight:300;color:#222;line-height:16px}
.blog-item p{font-size:8.3px;font-weight:300;line-height:16px;color:var(--body)}
.social-row{left:328px;display:flex;gap:10px;width:215px}
.social-tile{width:56px;height:45px;flex:none}
.social-row p{font-size:8.3px;font-weight:300;line-height:16px;color:var(--body);margin-top:4px}
.photo{width:96px;height:81px}
.footer{left:71px;top:980px;width:712px;height:178px;background:var(--footer)}
.footer-brand{left:86px;top:1004px;font-size:13px;font-weight:700;color:#aaa;display:flex;align-items:center;gap:5px}
.footer-brand span{width:9px;height:9px;background:#aaa}
.footer-tag{left:86px;top:1022px;font-size:6px;color:#888}
.footer-text{left:84px;top:1043px;width:222px;font-size:8.3px;font-weight:300;line-height:19px;color:var(--footer-text)}
.quick-title{left:355px;top:996px;font-size:12.5px;color:#ddd}
.quick-links{left:355px;top:1021px;list-style:none;font-size:8.3px;font-weight:300;line-height:19px;color:var(--footer-text)}
.manager-photo{left:513px;top:990px;width:129px;height:152px;background:linear-gradient(160deg,#6b5a50,#3a2c26 60%,#1d1a18)}
.manager-name{left:657px;top:990px;font-size:12.5px;line-height:17px;color:#fff}
.manager-info{left:657px;top:1031px;list-style:none;font-size:8.3px;font-weight:300;line-height:19px;color:var(--footer-text)}
.copyright{left:86px;top:1172px;font-size:7.5px;color:#222}
.foot-icons{left:711px;top:1170px;display:flex;gap:14px}
.foot-icons span{width:10px;height:10px;background:#222}
</style>
</head>
<body>
<header>
  <div class="abs topbar"></div>
  <div class="abs contact-item" style="left:86px"><span class="contact-icon"></span>(555) 204-7731</div>
  <div class="abs contact-item" style="left:166px"><span class="contact-icon"></span>support@brookvale.example</div>
  <div class="abs social-dots"><span></span><span></span><span></span><span></span><span></span><span></span><span></span></div>
  <div class="abs brand">
    <div class="brand-name"><span class="brand-mark"></span>Brookvale Funding</div>
    <div class="brand-tag">A Northfield Capital Company</div>
  </div>
  <nav class="abs nav">
    <a class="active">Home</a><a>About</a><a>Builders</a><a>Mortage Info</a><a>Approval Blog</a><a>Contact Info</a>
  </nav>
</header>

<section>
  <div class="abs hero-shadow"></div>
  <div class="abs hero-photo" role="img" aria-label="Two-storey stucco family home under a blue sky with palms and shrubs"></div>
  <div class="abs hero-panel">
    <h1 class="hero-title">Earning Your Business</h1>
    <p class="hero-text">Lorem Ipsum is simply dummy text of the printing and typesetting industry. Lorem Ipsum has been the industry's standard dummy text ever since the 1500s, when an unknown printer took a galley of type and scrambled it to make a type specimen book. It has survived not only five centuries, but also the leap into electronic typesetting.</p>
    <div class="hero-actions"><span class="btn-start">Start Here</span><span class="btn-know">Get to Know Us</span></div>
  </div>
</section>

<section>
  <div class="abs cred"></div>
  <div class="abs cred-panel"></div>
  <svg class="abs cred-notch" width="16" height="32" viewBox="0 0 16 32"><polygon points="0,0 14,0 14,14 0,32" fill="#fff"/><polygon points="0,0 14,14 0,30" fill="#f1f1f1"/></svg>
  <h2 class="abs cred-title">Our Credentials</h2>
  <p class="abs cred-text">Lorem Ipsum is simply dummy text of the printing and typesetting industry. Lorem Ipsum has been the industry's standard dummy text ever since the 1500s, when an unknown printer took a galley of type and scrambled it to make a type specimen book. It has survived not only five centuries, but also the leap into electronic typesetting, remaining essentially unchanged. It was popularised in the 1960s with the release of Letraset sheets containing Lorem Ipsum passages, and more recently.</p>
  <div class="abs feature" style="left:357px;top:482px">
    <svg class="feature-icon" width="72" height="72" viewBox="0 0 72 72" role="img" aria-label="Award ribbon icon">
      <rect width="72" height="72" fill="var(--red)"/>
      <polygon points="26,38 16,60 24,57 28,65 36,44" fill="#fff"/>
      <polygon points="46,38 56,60 48,57 44,65 36,44" fill="#fff"/>
      <polygon fill="#fff" points="36,10 39,15 44,12 45,18 51,17 49,23 55,25 50,29 54,34 48,35 49,41 43,40 41,45 36,42 31,45 29,40 23,41 24,35 18,34 22,29 17,25 23,23 21,17 27,18 28,12 33,15"/>
      <circle cx="36" cy="28" r="9" fill="none" stroke="var(--red)" stroke-width="1.5"/>
    </svg>
    <h3 class="feature-title">Awards</h3>
    <p class="feature-text">Lorem Ipsum is simply dummy text of the printing and typesetting industry. Lorem Ipsum has been the industry's standard dummy text ever.</p>
    <span class="btn-more">Read More</span>
  </div>
  <div class="abs feature" style="left:575px;top:482px">
    <svg class="feature-icon" width="72" height="72" viewBox="0 0 72 72" role="img" aria-label="Safe vault icon">
      <rect width="72" height="72" fill="var(--red)"/>
      <rect x="16" y="12" width="40" height="48" rx="6" fill="none" stroke="#fff" stroke-width="4"/>
      <circle cx="36" cy="36" r="11" fill="none" stroke="#fff" stroke-width="3"/>
      <circle cx="36" cy="36" r="3" fill="#fff"/>
      <g stroke="#fff" stroke-width="2.5">
        <line x1="36" y1="25" x2="36" y2="47"/><line x1="25" y1="36" x2="47" y2="36"/>
        <line x1="28.2" y1="28.2" x2="43.8" y2="43.8"/><line x1="43.8" y1="28.2" x2="28.2" y2="43.8"/>
      </g>
      <rect x="51" y="22" width="3" height="8" fill="#fff"/><rect x="51" y="42" width="3" height="8" fill="#fff"/>
    </svg>
    <h3 class="feature-title">Recognition</h3>
    <p class="feature-text">Lorem Ipsum is simply dummy text of the printing and typesetting industry. Lorem Ipsum has been the industry's standard dummy text ever.</p>
    <span class="btn-more">Read More</span>
  </div>
</section>

<section>
  <h2 class="abs sec-title" style="left:73px;width:213px;color:var(--red);border-color:var(--red)">Blog</h2>
  <div class="abs blog-item" style="top:764px"><h3>Borrwoing</h3><p>Lorem Ipsum is simply dummy text of the<br>printing and typesetting industry.</p></div>
  <div class="abs blog-item" style="top:829px"><h3>Announcements</h3><p>Lorem Ipsum is simply dummy text of the<br>printing and typesetting industry.</p></div>
  <div class="abs blog-item" style="top:892px"><h3>Builders Info</h3><p>Lorem Ipsum is simply dummy text of the<br>printing and typesetting industry.</p></div>

  <h2 class="abs sec-title" style="left:328px;width:213px;color:#333;border-color:#333">Social</h2>
  <div class="abs social-row" style="top:766px"><div class="social-tile" style="background:#0e76a8" role="img" aria-label="Professional network link"></div><p>Lorem Ipsum is simply dummy text of the printing and typesetting.</p></div>
  <div class="abs social-row" style="top:829px"><div class="social-tile" style="background:#5a6fd6" role="img" aria-label="Microblog link"></div><p>Lorem Ipsum is simply dummy text of the printing and typesetting.</p></div>
  <div class="abs social-row" style="top:894px"><div class="social-tile" style="background:#333" role="img" aria-label="Social network link"></div><p>Lorem Ipsum is simply dummy text of the printing and typesetting.</p></div>

  <h2 class="abs sec-title" style="left:579px;width:206px;color:var(--blue);border-color:var(--blue)">In the Community</h2>
  <div class="abs photo" style="left:578px;top:766px;background:linear-gradient(135deg,#c8463a,#3a8a4a 50%,#e0b64a)" role="img" aria-label="Group of children joining hands in a circle"></div>
  <div class="abs photo" style="left:688px;top:766px;background:linear-gradient(135deg,#d9b9a0,#6e4a33 60%,#3f3a2c)" role="img" aria-label="Cupped hands holding a seedling in soil"></div>
  <div class="abs photo" style="left:578px;top:861px;background:linear-gradient(180deg,#2f7fd0,#7fb7ea 55%,#0e2740 80%)" role="img" aria-label="Silhouetted crowd cheering against a blue sky"></div>
  <div class="abs photo" style="left:688px;top:861px;background:linear-gradient(135deg,#cfc6b8,#7a6a58 55%,#3b3530)" role="img" aria-label="Two men shaking hands at a community event"></div>
</section>

<footer>
  <div class="abs footer"></div>
  <div class="abs footer-brand">Brookvale Funding<span></span></div>
  <div class="abs footer-tag">A Northfield Capital Company</div>
  <p class="abs footer-text">Lorem Ipsum is simply dummy text of the printing and typesetting industry. Lorem Ipsum has been the industry's standard dummy text ever since the 1500s, when an unknown printer took a galley of type and scrambled it to make a type specimen book.</p>
  <h3 class="abs quick-title">Quick Link</h3>
  <ul class="abs quick-links"><li>Home</li><li>About</li><li>Builders</li><li>Mortagage Info</li><li>Approval Blogs</li><li>Contact us</li></ul>
  <div class="abs manager-photo" role="img" aria-label="Portrait of the branch manager"></div>
  <div class="abs manager-name">Marisol Kettering,<br>Branch Manager</div>
  <ul class="abs manager-info"><li>Office: 555.318.4420</li><li>Cell: 555.610.2294</li><li>mkettering@brookvale.example</li><li>NMLS: 40917</li><li>2218 Larkspur Row, Ste. 140</li><li>Cedar Hollow, TX 75990</li></ul>
  <div class="abs copyright">Copyright © Brookvale Funding. All Rights Reserved.</div>
  <div class="abs foot-icons"><span></span><span></span><span style="border-radius:50%"></span></div>
</footer>
</body>
</html>
```